Veranix - Solution provider in business consulting

Veranix is a swiss based company providing solutions for developing markets. The business covers various fields of business consulting, such as supply chain, product costs, quality management and manufacturing management. The Business operates in a efficient, straight and solution oriented manner.
The final design should communicate these characteristics. Asian people as well as as western people shall identify the qualities of the company at first sight.
The customer needs business cards with a simple view but an recognizable design, printed in high quality. Engraved elements such as the globe or simple words are possible.
Available colors are: (RAL)
102/102/102
51/102/102
153/204/153
255/102/51
Font: Calibri

```html
<!DOCTYPE html>
<html lang="en">
<head>
<meta charset="utf-8">
<title>Veranix – Business Cards</title>
<link href="https://fonts.googleapis.com/css2?family=Carlito:wght@400;700&display=swap" rel="stylesheet">
<style>
  :root {
    --stage: #e9e7e3;
    --card-grey: #666666;
    --card-white: #ffffff;
    --ink: #666666;
    --ink-soft: #9a9a9a;
    --globe-tint: #ececec;
    --on-dark: #ffffff;
  }
  * { margin: 0; padding: 0; box-sizing: border-box; }
  html, body {
    width: 1200px; height: 950px; overflow: hidden;
    background: var(--stage);
    font-family: "Carlito", "Calibri", Arial, sans-serif;
  }
  .stage { position: relative; width: 1200px; height: 950px; }
  .card {
    position: absolute; width: 660px; height: 410px;
    box-shadow: 0 6px 18px rgba(0,0,0,.18);
    overflow: hidden;
  }
  /* back side */
  .card--back { left: 140px; top: 50px; background: var(--card-grey); }
  .brand {
    position: absolute; display: flex; align-items: center; gap: 10px;
    font-weight: 400; letter-spacing: .5px; white-space: nowrap;
  }
  .card--back .brand {
    left: 50%; top: 150px; transform: translateX(-50%);
    color: var(--on-dark); font-size: 52px;
  }
  .brand__dot { width: 34px; height: 34px; border-radius: 50%; background: currentColor; }
  .card--back .web {
    position: absolute; left: 0; right: 0; top: 282px; text-align: center;
    color: var(--on-dark); font-size: 17px; letter-spacing: 3px;
  }
  /* front side */
  .card--front { left: 400px; top: 490px; background: var(--card-white); }
  .globe-mark { position: absolute; left: 330px; top: -40px; }
  .card--front .brand { left: 50px; top: 100px; color: var(--ink); font-size: 46px; }
  .card--front .brand__dot { width: 30px; height: 30px; }
  .person { position: absolute; right: 45px; top: 140px; text-align: right; color: var(--ink); }
  .person__name { font-weight: 700; font-size: 22px; }
  .person__role { font-size: 14px; color: var(--ink-soft); margin-top: 2px; }
  .contact {
    position: absolute; left: 50px; top: 228px; color: var(--ink);
    font-size: 15px; line-height: 20px; font-style: normal;
  }
  .contact__company { font-weight: 700; }
  .contact__lines { margin-top: 6px; list-style: none; }
  .contact__lines li { display: flex; align-items: center; gap: 8px; }
  .contact__lines svg { width: 13px; height: 13px; fill: var(--ink); flex: none; }
</style>
</head>
<body>
<main class="stage">
  <section class="card card--back" aria-label="Business card back">
    <div class="brand"><span>veranix</span><span class="brand__dot"></span></div>
    <p class="web">www.veranix.ch</p>
  </section>

  <section class="card card--front" aria-label="Business card front">
    <svg class="globe-mark" width="400" height="400" viewBox="0 0 400 400" aria-hidden="true">
      <circle cx="200" cy="200" r="190" fill="var(--globe-tint)"/>
    </svg>
    <div class="brand"><span>veranix</span><span class="brand__dot"></span></div>
    <div class="person">
      <p class="person__name">Marco Lenz</p>
      <p class="person__role">CEO</p>
    </div>
    <address class="contact">
      <p class="contact__company">Veranix GmbH</p>
      <p>Lindenweg 8, 9999 Aubach</p>
      <p>Switzerland</p>
      <ul class="contact__lines">
        <li><svg viewBox="0 0 16 16"><path d="M3 1h3l1 4-2 1c1 2 3 4 5 5l1-2 4 1v3c0 1-1 2-2 2C7 15 1 9 1 3c0-1 1-2 2-2z"/></svg>+41 71 555 0142</li>
        <li><svg viewBox="0 0 16 16"><path d="M4 0h8a1 1 0 0 1 1 1v14a1 1 0 0 1-1 1H4a1 1 0 0 1-1-1V1a1 1 0 0 1 1-1zm1 2v10h6V2zm3 11a1 1 0 1 0 0 2 1 1 0 0 0 0-2z"/></svg>+41 79 555 0187</li>
        <li><svg viewBox="0 0 16 16"><path d="M0 3h16v1L8 9 0 4zm0 3 8 5 8-5v7H0z"/></svg>marco.lenz@veranix.ch</li>
        <li><svg viewBox="0 0 16 16"><path d="M8 0a8 8 0 1 0 0 16A8 8 0 0 0 8 0zm0 2a6 6 0 0 1 5.6 4H11a9 9 0 0 0-1.5-3.8A6 6 0 0 1 8 2zM2.4 10h2.5a9 9 0 0 0 1.6 3.8A6 6 0 0 1 2.4 10zM2.4 6a6 6 0 0 1 4-3.8A9 9 0 0 0 4.9 6zM7 10h2c-.2 1.5-.6 2.8-1 3.6-.4-.8-.8-2.1-1-3.6zm0-4c.2-1.5.6-2.8 1-3.6.4.8.8 2.1 1 3.6zm4 4h2.6a6 6 0 0 1-4.1 3.8A9 9 0 0 0 11 10z"/></svg>www.veranix.ch</li>
      </ul>
    </address>
  </section>
</main>
</body>
</html>
```